Tech business card design

We need an amazing business card design for our new business 'Pexla' a marketing tech startup based in Sydney, Australia. We provide an online marketplace for businesses to search and buy advertising media, connect with service providers and learn more about marketing. We wish to communicate 'cool tech', reliability and professionalism and design based around our logo.

Target Market(s)

Business Owners

Contact Information for Business Card

Name
Position
Email Address
Website
Phone Number

Font styles to use
Other font styles liked:
• Avenir & Avenir Next

Colors

Designer to choose colors to be used in the design.

```html
<!DOCTYPE html>
<html lang="en">
<head>
<meta charset="utf-8">
<title>Pexla Business Card</title>
<link href="https://fonts.googleapis.com/css2?family=Nunito+Sans:wght@400;600;800&display=swap" rel="stylesheet">
<style>
  :root {
    --backdrop: #2b2b2d;
    --navy: #14204a;
    --navy-deep: #0f1a40;
    --paper: #ffffff;
    --ink: #1b1f2e;
    --ink-soft: #3a3f52;
    --rule: #8a8fa3;
  }
  html, body {
    margin: 0;
    width: 1200px;
    height: 582px;
    overflow: hidden;
    background: var(--backdrop);
    font-family: "Nunito Sans", "Avenir Next", Avenir, sans-serif;
  }
  .stage {
    position: relative;
    width: 1200px;
    height: 582px;
    display: flex;
    align-items: center;
    justify-content: center;
    gap: 60px;
  }
  .card {
    position: relative;
    width: 500px;
    height: 286px;
    border-radius: 26px;
    box-sizing: border-box;
    overflow: hidden;
  }
  .card--back { background: var(--navy); color: var(--paper); }
  .card--front { background: var(--paper); color: var(--ink); }

  .wordmark {
    position: absolute;
    left: 38px;
    top: 70px;
    font-weight: 800;
    font-size: 84px;
    line-height: 1;
    letter-spacing: -2px;
  }
  .card--front .wordmark { color: var(--navy-deep); }
  .card--back .wordmark { color: var(--paper); top: 100px; }

  .identity {
    position: absolute;
    left: 272px;
    top: 138px;
    width: 200px;
  }
  .card--back .identity { top: 80px; }
  .identity__name {
    font-weight: 600;
    font-size: 19px;
    letter-spacing: 0.5px;
    text-transform: uppercase;
    line-height: 1.1;
  }
  .identity__role {
    font-size: 12px;
    color: var(--ink-soft);
    padding-bottom: 5px;
    border-bottom: 1px dotted var(--rule);
  }
  .card--back .identity__role { color: #c9cde0; border-color: #6d77a0; }

  .contacts {
    list-style: none;
    margin: 12px 0 0;
    padding: 0;
    font-size: 12.5px;
    color: var(--ink-soft);
  }
  .card--back .contacts { color: #dfe2ee; }
  .contacts li {
    display: flex;
    align-items: center;
    gap: 7px;
    height: 17px;
  }
  .contacts svg { width: 12px; height: 12px; flex: none; }
  .icon-box { fill: var(--navy); }
  .icon-mark { fill: none; stroke: var(--paper); stroke-width: 1.3; }
  .card--back .icon-box { fill: var(--paper); }
  .card--back .icon-mark { stroke: var(--navy); }
</style>
</head>
<body>
<main class="stage">
  <section class="card card--back" aria-label="Card back">
    <div class="wordmark">Pexla</div>
    <div class="identity">
      <div class="identity__name">Marcus Lane</div>
      <div class="identity__role">Managing Director</div>
    </div>
  </section>

  <section class="card card--front" aria-label="Card front">
    <div class="wordmark">Pexla</div>
    <div class="identity">
      <div class="identity__name">Marcus Lane</div>
      <div class="identity__role">Managing Director</div>
      <ul class="contacts">
        <li>
          <svg viewBox="0 0 12 12" aria-hidden="true"><rect class="icon-box" width="12" height="12" rx="1.5"/><path class="icon-mark" d="M3 4.5c0-1 1-1.5 3-1.5s3 .5 3 1.5M3.5 5h5l.5 4h-6z"/></svg>
          <span>000-555-0142</span>
        </li>
        <li>
          <svg viewBox="0 0 12 12" aria-hidden="true"><rect class="icon-box" width="12" height="12" rx="1.5"/><path class="icon-mark" d="M2.5 3.5h7v5h-7zM2.5 3.5l3.5 3 3.5-3"/></svg>
          <span>info@pexlamail.com</span>
        </li>
        <li>
          <svg viewBox="0 0 12 12" aria-hidden="true"><rect class="icon-box" width="12" height="12" rx="1.5"/><circle class="icon-mark" cx="6" cy="6" r="3.5"/><path class="icon-mark" d="M2.5 6h7M6 2.5c-1.6 2-1.6 5 0 7M6 2.5c1.6 2 1.6 5 0 7"/></svg>
          <span>www.pexlamail.com</span>
        </li>
      </ul>
    </div>
  </section>
</main>
</body>
</html>
```